Business Card for a mobile physiotherapy company

I need a layout for a business card for a mobile physiotherapy company.
Slogan is "Mobile Physiotherapy - Your Road To Recovery"
Phone number is 867-555-0142
Email VardenTherapy@postnest.ca (subject to change with website)
Website www.VardenTherapy.ca
My name and credentials: Luke Varden Luke Varden, BSc(kin), MPT, CAFCI, IMS
Information maybe included: Direct Billing, Services including Physiotherapy, IMS, acupuncture
Maybe include facebook and instagram logos
One side with the logo clean and sharp
Other side with details, try not to look too busy, keep everything concise

```html
<!DOCTYPE html>
<html lang="en">
<head>
<meta charset="utf-8">
<title>Varden Therapy – Business Card</title>
<link href="https://fonts.googleapis.com/css2?family=Lora:wght@400;700&display=swap" rel="stylesheet">
<style>
  :root {
    --page: #c9c9cb;
    --teal: #1d5a54;
    --navy: #27456d;
    --ink-navy: #2b4370;
    --text-grey: #3d4047;
    --card-light: #f5f5f6;
    --card-light-edge: #e3e4e7;
    --white: #ffffff;
    --divider: #c9cbd0;
    --social-a: #2f9fe6;
    --social-b: #c23a8c;
  }
  * { margin: 0; padding: 0; box-sizing: border-box; }
  html, body { width: 1200px; height: 576px; overflow: hidden; }
  body {
    background: var(--page);
    font-family: "Lora", Georgia, serif;
    position: relative;
  }
  .card {
    position: absolute;
    top: 138px;
    border-radius: 13px;
    overflow: hidden;
    box-shadow: 0 3px 8px rgba(0,0,0,0.18);
  }
  /* Front */
  .card-front {
    left: 82px; width: 484px; height: 294px;
    background: linear-gradient(35deg, var(--teal) 0%, #22506a 55%, var(--navy) 100%);
    color: var(--white);
    text-align: center;
  }
  .front-name {
    position: absolute; left: 0; right: 0; top: 122px;
    font-size: 40px; line-height: 48px; font-weight: 700; color: var(--white);
  }
  .front-slogan { position: absolute; left: 0; right: 0; top: 184px; font-size: 11px; }
  .front-services { position: absolute; left: 0; right: 0; top: 262px; font-size: 12.5px; letter-spacing: 0.2px; }
  /* Back */
  .card-back {
    left: 602px; width: 480px; height: 291px;
    background: linear-gradient(160deg, var(--card-light) 0%, #eeeef0 55%, var(--card-light-edge) 100%);
  }
  .back-name {
    position: absolute; left: 16px; width: 222px; top: 116px;
    text-align: center; font-size: 26px; line-height: 32px; font-weight: 700; color: var(--ink-navy);
  }
  .back-divider { position: absolute; left: 239px; top: 72px; width: 1px; height: 134px; background: var(--divider); }
  .details { position: absolute; left: 269px; top: 66px; color: var(--text-grey); }
  .person-name { font-size: 19px; font-weight: 700; color: var(--ink-navy); letter-spacing: 0.5px; text-transform: uppercase; line-height: 24px; }
  .credentials { font-size: 10.5px; margin-top: 2px; }
  .social { display: flex; align-items: center; margin-top: 18px; font-size: 13px; }
  .social-dot { width: 20px; height: 20px; border-radius: 50%; margin-left: 5px; }
  .social-dot.one { margin-left: 6px; background: var(--social-a); }
  .social-dot.two { background: var(--social-b); }
  .contact-list { list-style: none; margin-top: 7px; }
  .contact-list li { display: flex; align-items: center; font-size: 13px; height: 17.5px; }
  .contact-list svg { width: 10px; height: 10px; margin-right: 13px; fill: var(--text-grey); }
  .back-band {
    position: absolute; left: 0; right: 0; bottom: 0; height: 27px;
    background: linear-gradient(90deg, var(--teal), var(--navy));
    color: var(--white); font-size: 13px; text-align: center; line-height: 27px;
  }
</style>
</head>
<body>
  <section class="card card-front" aria-label="Card front">
    <p class="front-name">Varden Therapy</p>
    <p class="front-slogan">Mobile Physiotherapy - Your Road To Recovery</p>
    <p class="front-services">Direct Billing &nbsp;|&nbsp; Services Including Physiotherapy &nbsp;|&nbsp; IMS &nbsp;|&nbsp; Acupuncture</p>
  </section>

  <section class="card card-back" aria-label="Card back">
    <p class="back-name">Varden Therapy</p>
    <div class="back-divider"></div>
    <div class="details">
      <h1 class="person-name">Luke Varden</h1>
      <p class="credentials">BSc(kin), MPT, CAFCI, IMS</p>
      <div class="social">
        <span>Follow us on:</span>
        <span class="social-dot one" role="img" aria-label="Social network link"></span>
        <span class="social-dot two" role="img" aria-label="Social network link"></span>
      </div>
      <ul class="contact-list">
        <li>
          <svg viewBox="0 0 10 10" aria-hidden="true"><path d="M1 3.5C1 2 2.5 1.5 5 1.5S9 2 9 3.5L7.5 4 7 3H3L2.5 4Z"/><rect x="2" y="4.5" width="6" height="4.5" rx="0.6"/></svg>
          867-555-0142
        </li>
        <li>
          <svg viewBox="0 0 10 10" aria-hidden="true"><path d="M0.5 2H9.5V8H0.5Z M1 2.4L5 5.6 9 2.4" stroke="#f5f5f6" stroke-width="0.7"/></svg>
          VardenTherapy@postnest.ca
        </li>
        <li>
          <svg viewBox="0 0 10 10" aria-hidden="true"><circle cx="5" cy="5" r="4.5"/><path d="M0.5 5H9.5M5 0.5V9.5M2.3 2.5H7.7M2.3 7.5H7.7" stroke="#f5f5f6" stroke-width="0.6" fill="none"/></svg>
          www.VardenTherapy.ca
        </li>
      </ul>
    </div>
    <div class="back-band">Mobile Physiotherapy - Your Road To Recovery</div>
  </section>
</body>
</html>
```